DESKHAVEN COSPACE Website design and coding

DESKHAVEN COSPACE

DESKHAVEN is Galveston’s first (and currently only) shared business co-working space. We share the same upscale, casual work environment, but we work independently on our own (or our team’s) projects and goals. For only a flat $195 membership fee per month, you have your very own all-inclusive, fun, personal business office environment. Website is written (Word file #12, below); and all pictures etc provided. Galveston is a beachy, coastal, historic city an hour from Houston, Texas USA. Logo (file 11 below) is temporary only.

Target Market(s)

Outside sales people, medical students looking for study hall, Houston companies looking for local office, real estate agents, graphic artists, entrepreneurs, etc

Contact Information for Business Card

will discuss --want to combine with current business card with multiple businesses

Logo Text

DESKHAVEN COSPACE

Coding

Coded - Design and coding required

Number of Pages Required

5+ page

Colors
ec1f27
fbed22

Requirements
Nice to have
• maroon/wine dominant with yellow and red accents, gray base are the colors of the space--website could coordinate--but open to creative ideas/combinations

```html
<!DOCTYPE html>
<html lang="en">
<head>
<meta charset="utf-8">
<title>Deskhaven Cospace</title>
<link href="https://fonts.googleapis.com/css2?family=Poppins:wght@300;400;500;600;700&family=Oswald:wght@500&family=Kreon:wght@400&display=swap" rel="stylesheet">
<style>
:root{
  --wine:#a30b0b;
  --red:#ec1f27;
  --yellow:#fbed22;
  --lemon:#fdfb6a;
  --ink:#111;
  --text:#555;
  --dark:#1b1a17;
  --field:#efefef;
  --blush:#f4e3e3;
}
*{margin:0;padding:0;box-sizing:border-box}
html,body{width:1200px;height:4118px;overflow:hidden}
body{position:relative;font-family:'Poppins',sans-serif;color:var(--text);background:#fff}
.abs{position:absolute}
.topbar{left:0;top:0;width:1200px;height:32px;background:#000}
.social{top:10px;width:12px;height:12px;border-radius:50%;background:#fff}
.header{left:0;top:32px;width:1200px;height:72px;background:#fff}
.brand{left:62px;top:44px;color:var(--wine);font-weight:700;font-size:22px;line-height:24px;letter-spacing:1px}
.brand small{display:block;font-size:13px;letter-spacing:3px;padding-left:20px}
.hc{top:50px;display:flex;align-items:center;gap:12px;font-size:12px;color:#666}
.hc .ic{width:40px;height:40px;border-radius:50%;border:2px solid var(--red);display:flex;align-items:center;justify-content:center}
.nav{left:200px;top:104px;width:665px;height:37px;background:var(--wine);display:flex;align-items:center;gap:24px;padding-left:24px;font-size:12px;color:#fff}
.nav-cta{left:865px;top:104px;width:134px;height:37px;background:var(--yellow);color:var(--wine);font-size:15px;display:flex;align-items:center;justify-content:center}
.hero{left:0;top:104px;width:1200px;height:638px;background:radial-gradient(ellipse at 45% 30%,#6b5a3c 0%,#3a3225 45%,#16140f 100%)}
.hero h1{position:absolute;left:0;top:250px;width:1200px;text-align:center;font-family:'Oswald',sans-serif;font-weight:500;font-size:44px;line-height:54px;color:var(--yellow)}
.btn{background:var(--wine);color:#fff;font-size:15px;display:flex;align-items:center;justify-content:center;font-weight:500}
.photo{display:block}
.serif{font-family:'Kreon',serif;color:var(--ink);font-weight:400}
.p{font-size:12.5px;line-height:19.5px;color:#666}
.amen{left:0;top:1267px;width:1200px;height:464px;background:linear-gradient(90deg,#141410 0%,#2a2921 55%,#3b392f 100%)}
.amen h2{position:absolute;left:61px;top:70px;font-size:30px;color:#fff}
.amen ul{position:absolute;left:61px;top:116px;list-style:none;color:#fff;font-size:12px}
.amen li{display:flex;gap:12px;align-items:flex-start;min-height:30px;width:520px;line-height:19px}
.amen li svg{flex:none;margin-top:2px}
.sect-title{left:0;width:1200px;text-align:center;font-size:30px}
.card{width:329px;height:475px;background:#fff;box-shadow:0 0 8px rgba(0,0,0,.18)}
.card .img{position:absolute;left:8px;top:8px;width:313px;height:225px}
.card .badge{position:absolute;right:24px;top:212px;width:48px;height:48px;border-radius:50%;background:#fff;box-shadow:0 2px 6px rgba(0,0,0,.25);display:flex;align-items:center;justify-content:center}
.card h3{position:absolute;left:18px;top:280px;font-size:15px;font-weight:500;color:var(--ink)}
.card p{position:absolute;left:18px;top:312px;width:292px;font-size:11.5px;line-height:19.5px;color:#777}
.card .more{position:absolute;left:8px;top:422px;width:313px;height:35px;background:var(--field);font-size:14px;color:var(--ink);display:flex;align-items:center;padding-left:10px}
.card .more span{position:absolute;right:0;top:0;width:56px;height:35px;background:var(--wine);clip-path:polygon(18% 0,100% 0,100% 100%,0 100%);display:flex;align-items:center;justify-content:center}
.band{left:0;top:2451px;width:1200px;height:187px;background:var(--lemon)}
.band p{position:absolute;left:61px;top:57px;width:680px;font-size:22px;line-height:30px;font-weight:600;color:var(--wine)}
.gallery{left:110px;top:2760px;width:978px;height:476px;background:#fff;box-shadow:0 0 8px rgba(0,0,0,.15)}
.cell{position:absolute;width:315px;height:225px}
.form{left:211px;top:3351px;width:452px;height:337px;background:#fff;box-shadow:0 0 10px rgba(0,0,0,.2)}
.form h2{position:absolute;left:21px;top:30px;font-size:30px}
.field{position:absolute;height:33px;background:var(--field);font-size:11.5px;color:#888;padding:8px 10px}
.footer{left:0;top:3763px;width:1200px;height:317px;background:var(--wine);color:#fff}
.footer h4{position:absolute;top:58px;font-size:17px;font-weight:500;color:var(--yellow)}
.footer ul{position:absolute;top:96px;list-style:none;font-size:11.5px;line-height:33px}
.fbrand{left:61px;top:58px;font-weight:700;font-size:26px;line-height:28px;letter-spacing:1px;color:#fff}
.fbrand small{display:block;font-size:14px;letter-spacing:3px;padding-left:20px}
.fc{left:888px;display:flex;gap:22px;font-size:11.5px;line-height:19px;width:300px}
.copy{left:0;top:4080px;width:1200px;height:38px;background:#000;color:#fff;font-size:11px;display:flex;align-items:center;justify-content:center}
</style>
</head>
<body>

<div class="abs topbar"></div>
<span class="abs social" style="left:1032px"></span>
<span class="abs social" style="left:1062px"></span>
<span class="abs social" style="left:1092px"></span>
<span class="abs social" style="left:1122px"></span>

<header class="abs header"></header>
<div class="abs brand">DESKHAVEN<small>COSPACE</small></div>
<div class="abs hc" style="left:606px">
  <span class="ic"><svg width="20" height="14" viewBox="0 0 20 14"><rect x="1" y="1" width="18" height="12" fill="var(--red)"/><path d="M1 1l9 7 9-7" stroke="#fff" stroke-width="1.5" fill="none"/></svg></span>
  hello@deskhavenmail.com
</div>
<div class="abs hc" style="left:847px">
  <span class="ic"><svg width="16" height="20" viewBox="0 0 16 20"><path d="M8 1a6 6 0 0 0-6 6c0 5 6 12 6 12s6-7 6-12a6 6 0 0 0-6-6z" fill="none" stroke="var(--red)" stroke-width="2"/><circle cx="8" cy="7" r="2" fill="var(--red)"/></svg></span>
  418 HARBOR AVE, STE. 7 GALVESTON, TX 77551
</div>

<div class="abs hero" role="img" aria-label="Photo of the lounge and shared kitchen of the coworking space at dusk">
  <h1>DESKHAVEN is Galveston’s first shared<br>business co-working space.</h1>
  <div class="abs btn" style="left:532px;top:376px;width:134px;height:36px">Learn More</div>
</div>
<nav class="abs nav"><span>Home</span><span>Amenities</span><span>Membership</span><span>pictures</span><span>The Deskhaven Philosophy</span></nav>
<div class="abs nav-cta">Contact Us</div>

<div class="abs" style="left:59px;top:839px;width:77px;height:329px;background:var(--blush)"></div>
<div class="abs photo" role="img" aria-label="Photo of the open office area with lockers and sofa" style="left:91px;top:817px;width:299px;height:262px;background:linear-gradient(160deg,#8a8680,#5a5650 50%,#2c2a27)"></div>
<div class="abs photo" role="img" aria-label="Photo of the lounge with white sofas and a desk chair" style="left:276px;top:954px;width:240px;height:254px;background:linear-gradient(170deg,#9a968f,#4d4a46 55%,#1f1e1c);border:3px solid #fff"></div>
<h2 class="abs serif" style="left:575px;top:872px;font-size:30px">Deskhaven Coworking</h2>
<p class="abs p" style="left:575px;top:925px;width:440px">DESKHAVEN is Galveston’s first (and currently only) shared business co-working space. We share the same upscale, casual work environment, but we work independently on our own (or our team’s) projects and goals. For only a flat $195 membership fee per month, you have your very own all-inclusive, fun, personal business office environment.</p>
<div class="abs btn" style="left:574px;top:1067px;width:134px;height:36px">Learn More</div>

<section class="abs amen" role="img" aria-label="Dim photo of the office interior with a potted plant">
  <h2 class="serif" style="color:#fff">Amenities</h2>
  <ul>
    <li><svg width="16" height="16" viewBox="0 0 16 16"><g fill="var(--yellow)"><rect x="6" y="0" width="4" height="4" transform="rotate(45 8 2)"/><rect x="6" y="12" width="4" height="4" transform="rotate(45 8 14)"/><rect x="0" y="6" width="4" height="4" transform="rotate(45 2 8)"/><rect x="12" y="6" width="4" height="4" transform="rotate(45 14 8)"/></g></svg>Open office or a private cubicle for your daily use.</li>
    <li><svg width="16" height="16" viewBox="0 0 16 16"><g fill="var(--yellow)"><rect x="6" y="0" width="4" height="4" transform="rotate(45 8 2)"/><rect x="6" y="12" width="4" height="4" transform="rotate(45 8 14)"/><rect x="0" y="6" width="4" height="4" transform="rotate(45 2 8)"/><rect x="12" y="6" width="4" height="4" transform="rotate(45 14 8)"/></g></svg>Free Wifi.</li>
    <li><svg width="16" height="16" viewBox="0 0 16 16"><g fill="var(--yellow)"><rect x="6" y="0" width="4" height="4" transform="rotate(45 8 2)"/><rect x="6" y="12" width="4" height="4" transform="rotate(45 8 14)"/><rect x="0" y="6" width="4" height="4" transform="rotate(45 2 8)"/><rect x="12" y="6" width="4" height="4" transform="rotate(45 14 8)"/></g></svg>24 hour access.</li>
    <li><svg width="16" height="16" viewBox="0 0 16 16"><g fill="var(--yellow)"><rect x="6" y="0" width="4" height="4" transform="rotate(45 8 2)"/><rect x="6" y="12" width="4" height="4" transform="rotate(45 8 14)"/><rect x="0" y="6" width="4" height="4" transform="rotate(45 2 8)"/><rect x="12" y="6" width="4" height="4" transform="rotate(45 14 8)"/></g></svg>Comfortable open casual spaces or private office cubicles – at your option</li>
    <li><svg width="16" height="16" viewBox="0 0 16 16"><g fill="var(--yellow)"><rect x="6" y="0" width="4" height="4" transform="rotate(45 8 2)"/><rect x="6" y="12" width="4" height="4" transform="rotate(45 8 14)"/><rect x="0" y="6" width="4" height="4" transform="rotate(45 2 8)"/><rect x="12" y="6" width="4" height="4" transform="rotate(45 14 8)"/></g></svg>Communal coffee bar and kitchen, with FREE coffee.</li>
    <li><svg width="16" height="16" viewBox="0 0 16 16"><g fill="var(--yellow)"><rect x="6" y="0" width="4" height="4" transform="rotate(45 8 2)"/><rect x="6" y="12" width="4" height="4" transform="rotate(45 8 14)"/><rect x="0" y="6" width="4" height="4" transform="rotate(45 2 8)"/><rect x="12" y="6" width="4" height="4" transform="rotate(45 14 8)"/></g></svg>Use of copier/printer (at per-copy cost).</li>
    <li><svg width="16" height="16" viewBox="0 0 16 16"><g fill="var(--yellow)"><rect x="6" y="0" width="4" height="4" transform="rotate(45 8 2)"/><rect x="6" y="12" width="4" height="4" transform="rotate(45 8 14)"/><rect x="0" y="6" width="4" height="4" transform="rotate(45 2 8)"/><rect x="12" y="6" width="4" height="4" transform="rotate(45 14 8)"/></g></svg>Keyless, digital door entry.</li>
    <li><svg width="16" height="16" viewBox="0 0 16 16"><g fill="var(--yellow)"><rect x="6" y="0" width="4" height="4" transform="rotate(45 8 2)"/><rect x="6" y="12" width="4" height="4" transform="rotate(45 8 14)"/><rect x="0" y="6" width="4" height="4" transform="rotate(45 2 8)"/><rect x="12" y="6" width="4" height="4" transform="rotate(45 14 8)"/></g></svg>Great opportunity for networking or mentoring.</li>
    <li><svg width="16" height="16" viewBox="0 0 16 16"><g fill="var(--yellow)"><rect x="6" y="0" width="4" height="4" transform="rotate(45 8 2)"/><rect x="6" y="12" width="4" height="4" transform="rotate(45 8 14)"/><rect x="0" y="6" width="4" height="4" transform="rotate(45 2 8)"/><rect x="12" y="6" width="4" height="4" transform="rotate(45 14 8)"/></g></svg>Great modern design – a place that looks “cutting edge” and which you will be proud to call your own</li>
  </ul>
</section>
<div class="abs" style="left:686px;top:1349px;width:428px;height:413px;background:var(--wine)"></div>
<div class="abs photo" role="img" aria-label="Photo of a private cubicle with a copier and the open office beyond" style="left:679px;top:1342px;width:428px;height:413px;background:linear-gradient(100deg,#bdb8ae,#8e8a82 45%,#c9c9c6 60%,#6f6e69)"></div>

<h2 class="abs serif sect-title" style="top:1836px">The Deskhaven Philosophy</h2>

<div class="abs card" style="left:69px;top:1895px">
  <div class="img" role="img" aria-label="Photo of a woman working at a laptop in a bright home office" style="background:linear-gradient(135deg,#f2f2f0,#cfcac4 60%,#8c7b6a)"></div>
  <div class="badge"><svg width="24" height="24"><circle cx="12" cy="12" r="9" fill="none" stroke="var(--red)" stroke-width="2"/></svg></div>
  <h3>Work outside the home</h3>
  <p>Free yourself for the burdens of house or school, and work in an environment that MOTIVATES you instead of DISTRACTS you. Meet like-minded people that can help you along, and yet you</p>
  <div class="more">Learn More<span><svg width="20" height="14"><path d="M2 7h15M11 2l6 5-6 5" stroke="#fff" stroke-width="2" fill="none"/></svg></span></div>
</div>
<div class="abs card" style="left:425px;top:1895px">
  <div class="img" role="img" aria-label="Photo of a businessman crossing a finish line in a stadium" style="background:linear-gradient(180deg,#2a3f6e,#1f5fa8 55%,#5a6b7c)"></div>
  <div class="badge"><svg width="24" height="24"><circle cx="12" cy="12" r="9" fill="none" stroke="var(--red)" stroke-width="2"/></svg></div>
  <h3>Deskhaven the competition</h3>
  <p>Because of the flexibility, prestigious location, opportunities to meet and network with active professionals, and the available tech and amenities, you have all the tools you need to excel in your chosen field.</p>
  <div class="more">Learn More<span><svg width="20" height="14"><path d="M2 7h15M11 2l6 5-6 5" stroke="#fff" stroke-width="2" fill="none"/></svg></span></div>
</div>
<div class="abs card" style="left:781px;top:1895px">
  <div class="img" role="img" aria-label="Photo of a group of coworkers gathered around a laptop" style="background:linear-gradient(135deg,#b46a4c,#e7e2dc 50%,#6e6a66)"></div>
  <div class="badge"><svg width="24" height="24"><circle cx="12" cy="12" r="9" fill="none" stroke="var(--red)" stroke-width="2"/></svg></div>
  <h3>Work your coworkers</h3>
  <p>DESKHAVEN is a community – if you are making a pot of (free) coffee – ask and make enough for everyone that wants some! You rapidly become part of more than an office – you have new friends, teachers,</p>
  <div class="more">Learn More<span><svg width="20" height="14"><path d="M2 7h15M11 2l6 5-6 5" stroke="#fff" stroke-width="2" fill="none"/></svg></span></div>
</div>

<section class="abs band">
  <p>For only $195 a month, charged to your credit card, you get the all-inclusive amenities listed above, for one flat fee. The only “extras” are for copies, on a per-copy basis.</p>
  <div class="abs btn" style="left:1003px;top:86px;width:136px;height:37px">Membership</div>
</section>

<h2 class="abs serif sect-title" style="top:2706px">The Deskhaven Philosophy</h2>
<div class="abs gallery">
  <div class="cell" role="img" aria-label="Photo of a meeting room behind glass doors" style="left:10px;top:10px;background:linear-gradient(160deg,#d7d3c8,#8a7f6b 55%,#3d3a33)"></div>
  <div class="cell" role="img" aria-label="Photo of long wooden work tables under pendant lamps" style="left:332px;top:10px;background:linear-gradient(170deg,#4a4438,#a5834b 55%,#2d2a25)"></div>
  <div class="cell" role="img" aria-label="Photo of the lounge with lockers and leather sofa" style="left:654px;top:10px;background:linear-gradient(170deg,#bdbab4,#5f5b55 55%,#24221f)"></div>
  <div class="cell" role="img" aria-label="Photo of the lounge corner with desks and sofas" style="left:10px;top:241px;background:linear-gradient(160deg,#c7c2b8,#5b5650 55%,#222)"></div>
  <div class="cell" role="img" aria-label="Photo of the kitchen bar and seating area" style="left:332px;top:241px;background:linear-gradient(170deg,#6b6456,#b09060 50%,#2e2b25)"></div>
  <div class="cell" role="img" aria-label="Photo of a high table with bar stools" style="left:654px;top:241px;background:linear-gradient(170deg,#a08250,#c9a669 50%,#4a3b27)"></div>
</div>

<div class="abs photo" role="img" aria-label="Photo of two colleagues reviewing a tablet together" style="left:663px;top:3377px;width:337px;height:255px;background:linear-gradient(135deg,#eef1f4,#b7c2cc 45%,#2b3a52)"></div>
<section class="abs form">
  <h2 class="serif">Get in touch</h2>
  <div class="field" style="left:18px;top:76px;width:203px">Name</div>
  <div class="field" style="left:228px;top:76px;width:203px">Email</div>
  <div class="field" style="left:18px;top:118px;width:203px">Phone no</div>
  <div class="field" style="left:228px;top:118px;width:203px">Contact Us</div>
  <div class="field" style="left:18px;top:158px;width:415px;height:73px">Massage</div>
  <div class="abs btn" style="left:20px;top:252px;width:111px;height:36px">Submit</div>
</section>

<footer class="abs footer">
  <div class="abs fbrand">DESKHAVEN<small>COSPACE</small></div>
  <p class="abs" style="left:61px;top:122px;width:225px;font-size:11.5px;line-height:19px">Lorem Ipsum is simply dummy text of the printing and typesetting industry. Lorem Ipsum has been the industry's standard</p>
  <h4 style="left:337px">Quick Links</h4>
  <ul style="left:337px"><li>- Home</li><li>- Amenities</li><li>- Membership</li><li>- pictures</li><li>- The Deskhaven Philosophy</li></ul>
  <h4 style="left:612px">Philosophy</h4>
  <ul style="left:612px"><li>- Work outside the home</li><li>- Deskhaven the competition</li><li>- Work your coworkers</li><li>- out path to your success</li><li>- The Deskhaven Philosophy</li></ul>
  <h4 style="left:888px">Contact us</h4>
  <div class="abs fc" style="top:96px"><svg width="16" height="20" viewBox="0 0 16 20"><path d="M8 1a6 6 0 0 0-6 6c0 5 6 12 6 12s6-7 6-12a6 6 0 0 0-6-6z" fill="#fff"/><circle cx="8" cy="7" r="2" fill="var(--wine)"/></svg><span>418 HARBOR AVE, STE. 7 GALVESTON,<br>TX 77551</span></div>
  <div class="abs fc" style="top:155px"><svg width="18" height="18" viewBox="0 0 18 18"><path d="M4 1l3 4-2 2c1 3 3 5 6 6l2-2 4 3-2 3C8 17 1 10 1 3z" fill="#fff"/></svg><span>409 555 0142</span></div>
  <div class="abs fc" style="top:210px"><svg width="20" height="14" viewBox="0 0 20 14"><rect x="1" y="1" width="18" height="12" fill="#fff"/><path d="M1 1l9 7 9-7" stroke="var(--wine)" stroke-width="1.5" fill="none"/></svg><span>hello@deskhavenmail.com</span></div>
</footer>
<div class="abs copy">© deskhaven cospace 2020. All Right Reserved</div>

</body>
</html>
```